Home Remodeling company needs a business card design

we need a business card design for home remodeling company in hamilton county, indiana USA. we offers a wide range of construction services including whole house renovations, Design and Build Basements and Kitchen and Bathroom Remodeling . we would like to see designs for both site of business card that use the same color of the company logo and also including all information below :
1- Karim Feltous CEO / General Contractor
2- all company contacts Telephone numbers ( 1-888-DULOM-47 ) ( 317-555-0193) email address ( info@dulomhome.com) website ( www.dulomhome.com ) and social media logos (Facebook- twitter- google plus )
3- company logo
4- licensed . insured . bonded

```html
<!DOCTYPE html>
<html lang="en">
<head>
<meta charset="utf-8">
<title>Dulom Home Remodeling – Business Cards</title>
<link href="https://fonts.googleapis.com/css2?family=Lato:ital,wght@0,400;0,700;1,400&display=swap" rel="stylesheet">
<style>
  :root {
    --backdrop: #e9e6e1;
    --card-white: #ffffff;
    --charcoal: #3a3b3d;
    --charcoal-light: #5b5c5f;
    --brand-red: #d2373f;
    --text-dark: #3b3b3b;
    --text-grey: #555555;
    --rule-grey: #bdbdbd;
  }
  * { margin: 0; padding: 0; box-sizing: border-box; }
  html, body { width: 1200px; height: 950px; overflow: hidden; }
  body {
    background: var(--backdrop);
    font-family: "Lato", Arial, sans-serif;
    position: relative;
  }
  .card {
    position: absolute;
    top: 325px;
    width: 525px;
    height: 300px;
    background: var(--card-white);
    box-shadow: 0 6px 18px rgba(0,0,0,0.18);
    overflow: hidden;
  }
  .card--contact { left: 45px; }
  .card--brand { left: 630px; }

  /* Contact side */
  .contact-shape { position: absolute; inset: 0; }
  .contact-block {
    position: absolute;
    left: 250px;
    top: 40px;
    color: var(--text-dark);
  }
  .person-name { font-size: 21px; font-weight: 700; }
  .person-title { font-size: 15px; color: var(--brand-red); margin-top: 3px; }
  .contact-list { list-style: none; margin-top: 14px; }
  .contact-list li {
    display: flex; align-items: center;
    font-size: 13px; color: var(--text-grey);
    height: 20px;
  }
  .contact-list li.indent { padding-left: 20px; }
  .contact-icon { width: 13px; height: 13px; margin-right: 7px; flex: none; }

  /* Brand side */
  .brand-name {
    position: absolute;
    left: 70px; top: 70px;
    font-size: 34px; font-weight: 700;
    color: var(--charcoal); line-height: 1.2;
  }
  .credentials {
    position: absolute; left: 70px; top: 150px;
    font-size: 17px; color: var(--brand-red); letter-spacing: 0.5px;
  }
  .services {
    position: absolute; left: 70px; top: 180px;
    font-size: 12.5px; font-style: italic; color: var(--text-grey); line-height: 1.45;
  }
  .social-row {
    position: absolute; left: 70px; top: 236px;
    display: flex; align-items: center; gap: 8px;
  }
  .social-rule { width: 70px; height: 1px; background: var(--rule-grey); }
  .social-dot { width: 16px; height: 16px; border-radius: 50%; background: var(--charcoal); }
</style>
</head>
<body>

<section class="card card--contact" aria-label="Business card, contact side">
  <svg class="contact-shape" width="525" height="300" viewBox="0 0 525 300" aria-hidden="true">
    <rect width="525" height="300" fill="var(--charcoal)"/>
    <polygon points="0,0 0,110 110,0" fill="var(--charcoal-light)"/>
    <polygon points="110,0 525,0 525,300 190,300 20,210 20,120" fill="var(--card-white)"/>
  </svg>
  <div class="contact-block">
    <p class="person-name">Karim Feltous</p>
    <p class="person-title">CEO / General Contractor</p>
    <ul class="contact-list">
      <li class="indent">1-888-DULOM-47</li>
      <li>
        <svg class="contact-icon" viewBox="0 0 16 16"><path d="M4 1l3 3-2 2c1 2 3 4 5 5l2-2 3 3-2 3C7 15 1 9 2 3z" fill="var(--brand-red)"/></svg>
        317-555-0193
      </li>
      <li>
        <svg class="contact-icon" viewBox="0 0 16 16"><rect x="1" y="3" width="14" height="10" fill="var(--brand-red)"/><path d="M1 3l7 6 7-6" stroke="#fff" stroke-width="1.4" fill="none"/></svg>
        info@dulomhome.com
      </li>
      <li>
        <svg class="contact-icon" viewBox="0 0 16 16"><circle cx="8" cy="8" r="7" fill="var(--brand-red)"/><path d="M1 8h14M8 1c-3 4-3 10 0 14M8 1c3 4 3 10 0 14" stroke="#fff" stroke-width="1" fill="none"/></svg>
        www.dulomhome.com
      </li>
    </ul>
  </div>
</section>

<section class="card card--brand" aria-label="Business card, brand side">
  <p class="brand-name">Dulom Home Remodeling</p>
  <p class="credentials">LICENSED | INSURED | BONDED</p>
  <p class="services">Construction services | Whole house renovations<br>Design &amp; Build Basements | Kitchen &amp; Bathroom Remodeling</p>
  <div class="social-row" aria-label="Social media">
    <span class="social-rule"></span>
    <span class="social-dot"></span>
    <span class="social-dot"></span>
    <span class="social-dot"></span>
    <span class="social-rule"></span>
  </div>
</section>

</body>
</html>
```